I need a business card designed using the logo provided either vertical or horizontal......Harbourline Property Group is an Australian based real estate company that caters for the upper end of the market so the design of the business card "must reflect" the companies image!!
Colour combinations are optional but "must be realistic" and must be able to be accurately useable CMYK colours.
Please consider that any colours used "must be able to be used" and be suitable in following designs for "pull out banner signs" and "real estate signs".
The colours and the font in the attached designs are for example and other combinations are encouraged.
Target Market(s)
The High End of the Australian real estate market
Industry/Entity Type
Business
Contact Information for Business Card
Logo - Business Name - Director + Licensed Real Estate Agent - Mobile Number (Cell Phone) - Business Number - Fax - Email Address - Web address
Requirements
Must have
- Designs and colours (CMYK) that can easily be interpreted by an Australian printer.
Nice to have
- Some alternative ideas on colour and font..........the ones provided are ok and have been provided as an example but I am looking for alternative ideas
Should not have
- Loud, overly bright colours. Designs that do not reflect the professional standards of the business.
- Designs that look good on a computer monitor but can not be re-created on a printing press.............this is most important when it comes to shading etc.

```html
<!DOCTYPE html>
<html lang="en">
<head>
<meta charset="utf-8">
<title>Harbourline Property Group – Business Card</title>
<link href="https://fonts.googleapis.com/css2?family=Montserrat:wght@500;600&family=Open+Sans:wght@400&display=swap" rel="stylesheet">
<style>
  :root {
    --backdrop: #3a3532;
    --card-black: #141414;
    --card-black-soft: #1e1e1e;
    --ink-white: #f2f2f2;
    --ink-grey: #9a9a9a;
    --ink-muted: #6e6e6e;
    --accent-red: #c0262d;
    --accent-gold: #c59a4a;
  }
  * { margin: 0; padding: 0; box-sizing: border-box; }
  html, body { width: 1200px; height: 844px; overflow: hidden; }
  body {
    background: var(--backdrop);
    display: flex;
    align-items: center;
    justify-content: center;
    gap: 60px;
  }
  .card {
    width: 525px;
    height: 300px;
    border-radius: 4px;
    background: linear-gradient(135deg, var(--card-black-soft), var(--card-black));
    box-shadow: 0 18px 40px rgba(0,0,0,0.45);
    position: relative;
  }
  /* Contact side */
  .card-back { padding: 48px 56px; }
  .person { width: max-content; }
  .person-name {
    font-family: "Montserrat", sans-serif;
    font-weight: 500;
    font-size: 19px;
    letter-spacing: 0.5px;
    color: var(--ink-white);
    text-transform: uppercase;
    padding-bottom: 4px;
    border-bottom: 1.5px solid var(--accent-red);
  }
  .person-title {
    font-family: "Open Sans", sans-serif;
    font-size: 14px;
    color: var(--ink-muted);
    margin-top: 4px;
    padding-left: 28px;
  }
  .contact-list {
    list-style: none;
    font-family: "Open Sans", sans-serif;
    font-size: 14px;
    line-height: 1.45;
    color: var(--ink-grey);
    text-align: center;
    margin-top: 26px;
  }
  .address {
    position: absolute;
    left: 56px;
    right: 56px;
    bottom: 30px;
    font-family: "Open Sans", sans-serif;
    font-size: 13px;
    color: var(--ink-grey);
    text-align: center;
  }
  /* Brand side */
  .card-front {
    display: flex;
    align-items: center;
    justify-content: center;
    background: radial-gradient(circle at 50% 35%, #262626, var(--card-black) 65%);
  }
  .brand {
    display: flex;
    align-items: center;
    gap: 12px;
  }
  .brand-square {
    width: 14px;
    height: 14px;
    background: var(--accent-gold);
  }
  .brand-name {
    font-family: "Montserrat", sans-serif;
    font-weight: 600;
    font-size: 20px;
    letter-spacing: 2px;
    color: var(--ink-white);
    text-transform: uppercase;
    line-height: 1.3;
  }
</style>
</head>
<body>
  <section class="card card-back">
    <div class="person">
      <h1 class="person-name">Callum Reid</h1>
      <p class="person-title">Managing Director</p>
    </div>
    <ul class="contact-list">
      <li>044-555-0192</li>
      <li>123-555-0148</li>
      <li>info@harbourlinegroup.com</li>
      <li>www.harbourlinegroup.com</li>
    </ul>
    <p class="address">48 Wharf Street | Sydney, NSW | 2000</p>
  </section>

  <section class="card card-front">
    <div class="brand">
      <span class="brand-square"></span>
      <span class="brand-name">Harbourline<br>Property Group</span>
    </div>
  </section>
</body>
</html>
```